Professional Photography Business cards

I need business cards that include my logo which I have uploaded. I run a photography business. I am open to ideas but I would like one side to have my logo and the other side to have my contact info. I don't have a website made but I do own a website domain. I have uploaded 2 different logo color schemes. My business colors are Blue, black , and white.

Business Name
Business Phone Number
Business Email
Business Website address
Instagram

Industry/Entity Type

Professional Photography

Contact Information for Business Card

Phone Number: 916-384-7702 email: info@tlane-studio.example Instagram: @t.lanestudio website doman- www.tlane-studio.example

Requirements
Must have
• I like the idea of a business card with a full black background front and back of card. My colors must include royal blue, black, and white

```html
<!DOCTYPE html>
<html lang="en">
<head>
<meta charset="utf-8">
<title>T. Lane Studio – Business Cards</title>
<link rel="stylesheet" href="https://fonts.googleapis.com/css2?family=Montserrat:wght@400;500;700&display=swap">
<style>
  :root {
    --backdrop: #e9eaec;
    --card-black: #060708;
    --royal-blue: #2b35b8;
    --ink-white: #f4f5f7;
    --muted-white: #d9dbe0;
    --card-shadow: rgba(0, 0, 0, 0.28);
  }
  * { box-sizing: border-box; margin: 0; padding: 0; }
  html, body {
    width: 1200px;
    height: 800px;
    overflow: hidden;
    background: var(--backdrop);
    font-family: "Montserrat", Arial, sans-serif;
  }
  .sheet {
    width: 1200px;
    height: 800px;
    display: flex;
    align-items: center;
    justify-content: center;
    gap: 48px;
  }
  .card {
    position: relative;
    width: 530px;
    height: 303px;
    background: var(--card-black);
    border-radius: 3px;
    box-shadow: 0 14px 30px var(--card-shadow);
    color: var(--ink-white);
  }

  /* Front */
  .card-front {
    display: flex;
    flex-direction: column;
    align-items: center;
    justify-content: center;
    gap: 26px;
  }
  .brand {
    display: flex;
    align-items: center;
    gap: 12px;
  }
  .brand-mark {
    border: 2px solid var(--ink-white);
    border-radius: 50%;
  }
  .brand-name {
    color: var(--royal-blue);
    font-weight: 500;
    letter-spacing: 0.04em;
  }
  .card-front .brand-mark { width: 38px; height: 38px; }
  .card-front .brand-name { font-size: 34px; }
  .social-handle {
    display: flex;
    align-items: center;
    gap: 8px;
    font-size: 14px;
    color: var(--ink-white);
  }
  .social-square {
    width: 12px;
    height: 12px;
    background: var(--ink-white);
    border-radius: 2px;
  }

  /* Back */
  .card-back {
    display: flex;
    align-items: center;
    padding: 0 36px 0 40px;
  }
  .card-back .brand { width: 205px; }
  .card-back .brand-mark { width: 24px; height: 24px; }
  .card-back .brand-name { font-size: 21px; }
  .divider {
    width: 1.5px;
    height: 150px;
    background: var(--royal-blue);
    margin: 0 22px 0 12px;
  }
  .contact { font-size: 12.5px; line-height: 1.45; color: var(--muted-white); }
  .contact-name {
    font-size: 16px;
    font-weight: 700;
    letter-spacing: 0.03em;
    color: var(--ink-white);
  }
  .contact-role {
    color: var(--royal-blue);
    font-size: 13px;
    margin-bottom: 6px;
  }
  .contact-address { margin-bottom: 2px; }
  .contact-line {
    display: flex;
    align-items: center;
    gap: 7px;
  }
  .contact-icon { width: 11px; height: 11px; fill: var(--ink-white); flex: none; }
</style>
</head>
<body>
  <main class="sheet">
    <section class="card card-front" aria-label="Card front">
      <div class="brand">
        <span class="brand-mark"></span>
        <span class="brand-name">T. Lane Studio</span>
      </div>
      <p class="social-handle"><span class="social-square"></span>@t.lanestudio</p>
    </section>

    <section class="card card-back" aria-label="Card back">
      <div class="brand">
        <span class="brand-mark"></span>
        <span class="brand-name">T. Lane Studio</span>
      </div>
      <span class="divider"></span>
      <div class="contact">
        <p class="contact-name">TESSA LANE</p>
        <p class="contact-role">Plant Manager</p>
        <p class="contact-address">4120 Birchwood Lane<br>Fair Oaks, CA 95628</p>
        <p class="contact-line">
          <svg class="contact-icon" viewBox="0 0 24 24" aria-hidden="true"><path d="M6.6 10.8a15.1 15.1 0 0 0 6.6 6.6l2.2-2.2c.3-.3.7-.4 1-.2 1.1.4 2.3.6 3.6.6.6 0 1 .4 1 1V20c0 .6-.4 1-1 1C10.6 21 3 13.4 3 4c0-.6.4-1 1-1h3.5c.6 0 1 .4 1 1 0 1.3.2 2.5.6 3.6.1.3 0 .7-.2 1z"/></svg>
          916.384.7702
        </p>
        <p class="contact-line">
          <svg class="contact-icon" viewBox="0 0 24 24" aria-hidden="true"><path d="M2 5h20v14H2z M4 7v.5l8 5 8-5V7l-8 5z" fill-rule="evenodd"/></svg>
          info@tlane-studio.example
        </p>
        <p class="contact-line">
          <svg class="contact-icon" viewBox="0 0 24 24" aria-hidden="true"><path d="M12 2a10 10 0 1 0 0 20 10 10 0 0 0 0-20zm0 2c.9 1.2 1.7 2.9 2 5h-4c.3-2.1 1.1-3.8 2-5zM4.3 13a8 8 0 0 1 0-2h3.7a18 18 0 0 0 0 2zm.7 2h3.2c.3 1.5.8 2.9 1.5 4A8 8 0 0 1 5 15zm3.2-6H5a8 8 0 0 1 4.7-4c-.7 1.1-1.2 2.5-1.5 4zM12 20c-.9-1.2-1.7-2.9-2-5h4c-.3 2.1-1.1 3.8-2 5zm2.3-7H9.7a16 16 0 0 1 0-2h4.6a16 16 0 0 1 0 2zm0 6c.7-1.1 1.2-2.5 1.5-4H19a8 8 0 0 1-4.7 4zm1.7-6a18 18 0 0 0 0-2h3.7a8 8 0 0 1 0 2zm-.2-4c-.3-1.5-.8-2.9-1.5-4A8 8 0 0 1 19 9z"/></svg>
          www.tlane-studio.example
        </p>
      </div>
    </section>
  </main>
</body>
</html>
```